Dovecote Realty

Business cards for 4 people

They need to say for all
87 Tarrow Quay, Boston MA 02114

Each person will have their own personal information
We would like gold embossing for the name of the company
Marla is the blonde sitting in the chair smiling her information should be on the back of the card with her name and information
Should say for slogan classic pattern, elevated experience
grace@dovecoteprops.com
(413) 555-0182

Odette is the brunette with wavy hair in the tan suit odette@dovecoteprops.com
(617) 555-0137

faith@dovecoteprops.com
(413) 555-0164
standing next to the chair

hope@dovecoteprops.com
(413) 555-0199
close up headshot

```html
<!DOCTYPE html>
<html lang="en">
<head>
<meta charset="utf-8">
<title>Dovecote Realty – Business Card</title>
<link rel="stylesheet" href="https://fonts.googleapis.com/css2?family=Open+Sans:wght@400;600;700&display=swap">
<style>
  :root {
    --backdrop: #e4dccf;
    --card-dark: #161616;
    --card-mid: #262626;
    --card-light: #383838;
    --gold: #c68d4c;
    --gold-soft: #b88448;
    --portrait-deep: #3a2a1e;
    --portrait-warm: #9a6a42;
  }
  * { margin: 0; padding: 0; box-sizing: border-box; }
  html, body {
    width: 1200px;
    height: 1046px;
    overflow: hidden;
    background: var(--backdrop);
    font-family: "Open Sans", Arial, sans-serif;
  }
  .card {
    position: absolute;
    left: 50px;
    top: 223px;
    width: 1100px;
    height: 600px;
    border-radius: 34px;
    overflow: hidden;
    background:
      radial-gradient(ellipse 55% 60% at 22% 88%, var(--card-light) 0%, transparent 70%),
      linear-gradient(120deg, var(--card-mid) 0%, var(--card-dark) 55%, #1b1b1b 100%);
    box-shadow: 0 18px 40px rgba(0,0,0,0.25);
  }
  .brand-ring {
    position: absolute;
    left: 163px;
    top: 31px;
    width: 132px;
    height: 132px;
    border: 3px solid var(--gold);
    border-radius: 50%;
  }
  .brand-name {
    position: absolute;
    left: 29px;
    top: 176px;
    width: 400px;
    text-align: center;
    white-space: nowrap;
    font-weight: 600;
    font-size: 32px;
    line-height: 44px;
    letter-spacing: 2px;
    text-transform: uppercase;
    color: var(--gold);
  }
  .agent-name {
    position: absolute;
    left: 46px;
    top: 260px;
    font-size: 50px;
    line-height: 60px;
    font-weight: 700;
    color: var(--gold);
    white-space: nowrap;
  }
  .agent-title {
    position: absolute;
    left: 47px;
    top: 322px;
    font-size: 22px;
    line-height: 30px;
    font-weight: 600;
    color: var(--gold-soft);
    white-space: nowrap;
  }
  .address {
    position: absolute;
    left: 46px;
    top: 377px;
    font-size: 28px;
    line-height: 34px;
    color: var(--gold-soft);
    white-space: nowrap;
  }
  .contacts {
    position: absolute;
    left: 42px;
    top: 470px;
    list-style: none;
    color: var(--gold-soft);
    font-size: 28px;
  }
  .contacts li {
    display: flex;
    align-items: center;
    height: 33px;
    white-space: nowrap;
  }
  .contacts svg {
    width: 24px;
    height: 24px;
    margin-right: 16px;
    flex: none;
  }
  .portrait {
    position: absolute;
    left: 638px;
    top: 116px;
    width: 462px;
    height: 484px;
    background:
      radial-gradient(ellipse 40% 45% at 55% 38%, var(--portrait-warm) 0%, transparent 75%),
      linear-gradient(180deg, #2a221c 0%, var(--portrait-deep) 45%, #8a5e3c 100%);
  }
</style>
</head>
<body>
  <main class="card">
    <span class="brand-ring"></span>
    <div class="brand-name">Dovecote Realty</div>

    <h1 class="agent-name">Odette Lavigne</h1>
    <p class="agent-title">Real Estate Advisor and Sales Manager</p>

    <p class="address">87 Tarrow Quay,<br>Boston MA 02114</p>

    <ul class="contacts">
      <li>
        <svg viewBox="0 0 24 24" fill="var(--gold-soft)" aria-hidden="true">
          <path d="M6.6 10.8a15.1 15.1 0 0 0 6.6 6.6l2.2-2.2a1 1 0 0 1 1-.25 11.4 11.4 0 0 0 3.6.57 1 1 0 0 1 1 1V20a1 1 0 0 1-1 1A17 17 0 0 1 3 4a1 1 0 0 1 1-1h3.5a1 1 0 0 1 1 1c0 1.25.2 2.450.57 3.57a1 1 0 0 1-.25 1z"/>
        </svg>
        (617) 555-0137
      </li>
      <li>
        <svg viewBox="0 0 24 24" fill="none" stroke="var(--gold-soft)" stroke-width="2" aria-hidden="true">
          <circle cx="12" cy="12" r="9.5"/>
          <ellipse cx="12" cy="12" rx="4" ry="9.5"/>
          <path d="M2.5 12h19"/>
        </svg>
        www.dovecoteprops.com
      </li>
      <li>
        <svg viewBox="0 0 24 24" fill="none" stroke="var(--gold-soft)" stroke-width="2" aria-hidden="true">
          <rect x="2.5" y="5" width="19" height="14" rx="1.5"/>
          <path d="M2.5 6l9.5 7 9.5-7"/>
        </svg>
        odette@dovecoteprops.com
      </li>
    </ul>

    <div class="portrait" role="img" aria-label="Portrait photo of Odette Lavigne, brunette with wavy hair in a tan suit"></div>
  </main>
</body>
</html>
```